Coastline Premier Retreats Business Card Design

Design a business card for Coastline Premier Retreats. Look at the website for colors and reference. Card should have logo, name, title, office number, mobile number, email, URL and a tagline like, "Luxury Hotel & Resort Email Marketing" (This might change).

https://www.coastlinepremierretreats.example

The rest I will leave up to your imagination.

Contact Information for Business Card

Logo, name, title, office number, mobile number, email, URL and a tagline like, "Luxury Hotel & Resort Email Marketing" (This might change).

```html
<!DOCTYPE html>
<html lang="en">
<head>
<meta charset="utf-8">
<title>Coastline Premier Retreats — Business Card</title>
<link rel="stylesheet" href="https://fonts.googleapis.com/css2?family=Open+Sans:wght@400;600;700;800&display=swap">
<style>
  :root {
    --stage: #222224;
    --card: #1d1d20;
    --panel: #242427;
    --layer-mid: #1f1f22;
    --layer-low: #1a1a1d;
    --orange: #f27a1a;
    --white: #f4f4f4;
    --emboss: #2b2b2f;
  }
  * { margin: 0; padding: 0; box-sizing: border-box; }
  html, body {
    width: 1200px; height: 780px; overflow: hidden;
    background: var(--stage);
    font-family: "Open Sans", Arial, sans-serif;
  }
  .stage {
    position: relative; width: 1200px; height: 780px;
    display: flex; justify-content: center; align-items: center; gap: 90px;
  }
  .card {
    position: relative; width: 380px; height: 640px;
    border-radius: 24px; overflow: hidden;
    background: var(--card);
    box-shadow: 0 18px 40px rgba(0,0,0,.55);
  }

  /* Back side */
  .card-back .brand-mark {
    position: absolute; left: 50%; top: 50%;
    transform: translate(-50%, -50%) rotate(-90deg);
    white-space: nowrap;
    font-weight: 800; font-size: 34px; letter-spacing: 2px;
    color: var(--emboss);
    text-transform: uppercase;
  }

  /* Front side */
  .card-front .layers { position: absolute; inset: 0; }
  .logo {
    position: absolute; top: 58px; left: 0; right: 0;
    display: flex; justify-content: center; align-items: center; gap: 10px;
  }
  .logo-square { width: 14px; height: 14px; background: var(--orange); }
  .logo-name {
    font-weight: 700; font-size: 17px; letter-spacing: 1.5px;
    color: var(--white); text-transform: uppercase;
  }
  .identity {
    position: absolute; top: 200px; left: 0; right: 0; text-align: center;
  }
  .person-name { font-weight: 800; font-size: 30px; line-height: 1.1; }
  .person-name .first { color: var(--orange); }
  .person-name .last { color: var(--white); }
  .person-title { color: var(--white); font-size: 15px; margin-top: 4px; }
  .contact-icons {
    display: flex; justify-content: center; gap: 8px; margin-top: 16px;
  }
  .contact-icons .icon {
    width: 22px; height: 22px; border-radius: 50%;
    background: var(--orange);
    display: flex; align-items: center; justify-content: center;
  }
  .contact-list {
    list-style: none; margin-top: 12px;
    color: var(--white); font-size: 13.5px; line-height: 1.55;
  }
  .tagline {
    position: absolute; bottom: 60px; left: 0; right: 0; text-align: center;
    color: var(--orange); font-size: 16px; font-weight: 600; line-height: 1.35;
  }
</style>
</head>
<body>
<main class="stage">

  <section class="card card-back" aria-label="Card back">
    <span class="brand-mark">Coastline Premier Retreats</span>
  </section>

  <section class="card card-front" aria-label="Card front">
    <svg class="layers" width="380" height="640" viewBox="0 0 380 640" aria-hidden="true">
      <defs>
        <filter id="layer-shadow" x="-20%" y="-20%" width="140%" height="140%">
          <feDropShadow dx="0" dy="8" stdDeviation="10" flood-color="#000" flood-opacity=".55"/>
        </filter>
      </defs>
      <rect width="380" height="640" fill="var(--layer-low)"/>
      <path d="M0 0 H380 V440 C320 520 230 570 0 610 Z" fill="var(--layer-mid)" filter="url(#layer-shadow)"/>
      <path d="M0 0 H380 V390 C360 470 290 520 170 525 H0 Z" fill="var(--panel)" filter="url(#layer-shadow)"/>
    </svg>

    <div class="logo">
      <span class="logo-square"></span>
      <span class="logo-name">Coastline Premier Retreats</span>
    </div>

    <div class="identity">
      <h1 class="person-name"><span class="first">Marina</span> <span class="last">Delacroix</span></h1>
      <p class="person-title">Co-Founder</p>

      <div class="contact-icons">
        <span class="icon" aria-label="Office phone">
          <svg width="12" height="12" viewBox="0 0 24 24"><path d="M6.6 10.8a15 15 0 0 0 6.6 6.6l2.2-2.2a1 1 0 0 1 1-.25 11.4 11.4 0 0 0 3.6.57 1 1 0 0 1 1 1V20a1 1 0 0 1-1 1A17 17 0 0 1 3 4a1 1 0 0 1 1-1h3.5a1 1 0 0 1 1 1c0 1.25.2 2.45.57 3.57a1 1 0 0 1-.25 1z" fill="#fff"/></svg>
        </span>
        <span class="icon" aria-label="Mobile phone">
          <svg width="12" height="12" viewBox="0 0 24 24"><rect x="6" y="2" width="12" height="20" rx="2" fill="none" stroke="#fff" stroke-width="2"/><circle cx="12" cy="18" r="1.2" fill="#fff"/></svg>
        </span>
        <span class="icon" aria-label="Email">
          <svg width="12" height="12" viewBox="0 0 24 24"><rect x="3" y="5" width="18" height="14" rx="1.5" fill="none" stroke="#fff" stroke-width="2"/><path d="M3 6l9 7 9-7" fill="none" stroke="#fff" stroke-width="2"/></svg>
        </span>
        <span class="icon" aria-label="Website">
          <svg width="12" height="12" viewBox="0 0 24 24"><circle cx="12" cy="12" r="9" fill="none" stroke="#fff" stroke-width="2"/><path d="M3 12h18M12 3c3 3 3 15 0 18M12 3c-3 3-3 15 0 18" fill="none" stroke="#fff" stroke-width="1.6"/></svg>
        </span>
      </div>

      <ul class="contact-list">
        <li>(555) 014-2758</li>
        <li>(555) 016-7777</li>
        <li>www.coastlinepremierretreats.example</li>
        <li>info@coastlinepremierretreats.example</li>
      </ul>
    </div>

    <p class="tagline">Luxury Hotel &amp;<br>Resort Email Marketing</p>
  </section>

</main>
</body>
</html>
```